Wordpress website design for children’s entertainment agency

What is the aim of the website?

The aim for the website is to attract potential bookers and to get them to respond to the Call to action: contact the entertainer - phone call/request a call back/completing a form.
All the information needs to be easy to access and navigate to, especially on mobile view.
The call to action needs to be clear and easy to navigate.

What I need:

Critical - This website needs to look good on all devices.
Easy navigation on a mobile device is essential so the elements need to be bold and easy to click on with a thumb (when in mobile view)

The ‘grid area’ needs to be graphics based with simple descriptions, i.e. ‘magic shows’, Circus Clowns, Face painting, Costume Characters, Party Host, Carnival Parties, Balloon Sculpting, DJ and MC, Princess Parties, Holiday Parties, Fun Add Ons and Contact.

See: http://www.jollymarvin.com/
and http://playtimebookingnest.com/

I would like to see a sample page layout as well to see how your design would be carried through the site layout in the inside pages.

Target Market(s)

The site visitors are mainly mums, aged between 25 - 41. Other visitors will included event organisers looking for entertainment services for baptism, communions and sweet 16’s

Industry/Entity Type

Entertainment Industry

Number of Pages Required

1 page

Font styles to use
Sans Serif

Colors
6c459b
fbed22
0493ce

Requirements
Must have
• Critical - This website needs to look good on all devices.
• Easy navigation on a mobile device is essential so the elements need to be bold and easy to click on with a thumb (when in mobile view)
• The ‘grid area’ needs to be graphics based with simple descriptions, i.e. ‘magic shows’, Circus Clowns, Face painting, Costume Characters, Party Host, Carnival Parties, Balloon Sculpting, DJ and MC, Princess Parties, Holiday Parties, Fun Add Ons and Contact.
• See: http://www.jollymarvin.com/
• and http://playtimebookingnest.com/
Nice to have
• clean looking and fun with an element of ‘Trobel’ and stars (this is the exciting site http://gordysjoyshack.com/index.html)

```html
<!DOCTYPE html>
<html lang="en">
<head>
<meta charset="utf-8">
<title>Pippas Party Parlor – Family Entertainment</title>
<link href="https://fonts.googleapis.com/css2?family=Montserrat:wght@400;600;700;800&family=Open+Sans:wght@400;600&display=swap" rel="stylesheet">
<style>
:root{
  --purple:#6c459b;
  --yellow:#fbed22;
  --blue:#0493ce;
  --ink:#2b2b2b;
  --grey-bg:#e4e4e4;
  --charcoal:#3a3a3a;
  --white:#ffffff;
}
*{box-sizing:border-box;margin:0;padding:0}
html,body{width:1200px;height:2924px;overflow:hidden;background:var(--white)}
body{font-family:"Open Sans",Arial,sans-serif;color:var(--ink);position:relative}

/* header */
.site-header{position:absolute;top:0;left:0;width:1200px;height:180px;background:var(--white)}
.brand{position:absolute;left:140px;top:30px;display:flex;align-items:center;gap:14px}
.brand-dot{width:44px;height:44px;border-radius:50%;background:var(--yellow);flex:none}
.brand-name{font-family:"Montserrat",Arial,sans-serif;font-weight:800;font-size:28px;line-height:1.05;color:var(--purple);width:170px}
.header-phone{position:absolute;right:152px;top:78px;font-family:"Montserrat",Arial,sans-serif;font-size:14px;letter-spacing:2px;color:var(--ink)}
.main-nav{position:absolute;right:152px;top:112px;display:flex;gap:34px}
.main-nav a{font-family:"Montserrat",Arial,sans-serif;font-weight:700;font-size:15px;letter-spacing:1.5px;color:var(--ink);text-decoration:none;white-space:nowrap}

/* hero */
.hero{position:absolute;top:180px;left:0;width:1200px;height:380px;background:var(--yellow)}
.hero-photo{position:absolute;left:0;top:0;width:400px;height:380px;background:radial-gradient(circle at 45% 40%,#e8372f 0,#c1272d 35%,#1a1a1a 75%)}
.hero-copy{position:absolute;left:592px;top:52px;width:560px}
.hero-title{font-family:"Montserrat",Arial,sans-serif;font-weight:700;font-size:34px;line-height:1.2;letter-spacing:4px;color:var(--purple)}
.hero-quote{margin-top:60px;font-family:"Montserrat",Arial,sans-serif;font-weight:600;font-size:18px;letter-spacing:2px;color:var(--ink)}
.btn{display:inline-block;background:var(--purple);color:var(--white);font-family:"Montserrat",Arial,sans-serif;font-weight:700;font-size:15px;letter-spacing:2px;border-radius:22px;text-align:center;white-space:nowrap}
.hero .btn{margin-top:34px;width:320px;height:44px;line-height:44px}

/* services */
.services-title{position:absolute;top:616px;left:0;width:1200px;text-align:center;font-family:"Montserrat",Arial,sans-serif;font-weight:700;font-size:30px;letter-spacing:5px;color:var(--purple)}
.services-rule{position:absolute;top:668px;left:570px;width:60px;height:3px;background:var(--purple)}
.service-grid{position:absolute;top:720px;left:0;width:1200px;display:grid;grid-template-columns:396px 400px 404px;grid-template-rows:312px 312px 308px;row-gap:4px}
.service{position:relative;overflow:hidden;margin-right:4px}
.service:nth-child(3n){margin-right:0}
.service-art{position:absolute;inset:0}
.service-label{position:absolute;left:0;right:0;bottom:0;height:48px;line-height:48px;background:var(--purple);color:var(--white);text-align:center;white-space:nowrap;font-family:"Montserrat",Arial,sans-serif;font-weight:800;font-size:27px;letter-spacing:2px}

/* welcome */
.welcome{position:absolute;top:1660px;left:0;width:1200px;height:400px;background:var(--white)}
.welcome-box{position:absolute;left:160px;top:20px;width:880px;height:360px;background:var(--grey-bg);padding:58px 80px}
.welcome-title{font-family:"Montserrat",Arial,sans-serif;font-weight:700;font-size:30px;letter-spacing:4px;color:#444;white-space:nowrap}
.welcome-text{margin-top:30px;font-size:15px;line-height:1.55;color:#555}
.welcome .btn{margin-top:34px;width:326px;height:42px;line-height:42px;font-size:14px}

/* contact strip */
.contact-strip{position:absolute;top:2060px;left:0;width:1200px;height:180px;background:var(--yellow)}
.contact-item{position:absolute;top:72px;display:flex;align-items:center;gap:22px;font-family:"Montserrat",Arial,sans-serif;font-weight:600;font-size:16px;letter-spacing:2px;color:var(--ink);white-space:nowrap}
.contact-item svg{flex:none}

/* form */
.say-hello{position:absolute;top:2240px;left:0;width:1200px;height:360px;background:var(--charcoal)}
.say-title{position:absolute;top:30px;left:0;width:1200px;text-align:center;font-family:"Montserrat",Arial,sans-serif;font-weight:400;font-size:22px;color:var(--white)}
.hello-form{position:absolute;left:390px;top:74px;width:458px}
.field{border:1px solid #8a8a8a;height:30px;color:#aaa;font-size:11px;padding:7px 8px}
.field-row{display:flex;gap:8px}
.field-row .field{flex:1}
.field-area{height:150px;margin-top:8px}
.form-submit{margin-top:8px;height:26px;border:1px solid #8a8a8a;text-align:center;line-height:24px;font-size:11px;letter-spacing:2px;color:var(--white)}

/* footer */
.site-footer{position:absolute;top:2600px;left:0;width:1200px;height:240px;background:var(--white)}
.site-footer .brand{left:152px;top:40px}
.footer-about{position:absolute;left:432px;top:36px;width:330px}
.footer-heading{font-family:"Montserrat",Arial,sans-serif;font-weight:700;font-size:15px;letter-spacing:2px;color:var(--ink)}
.footer-about p{margin-top:14px;font-size:12px;line-height:1.55;color:#555}
.footer-social{position:absolute;left:820px;top:36px}
.social-row{margin-top:16px;display:flex;gap:6px}
.social-row span{width:26px;height:26px;border:2px solid var(--ink);border-radius:50%}

.legal-bar{position:absolute;top:2840px;left:0;width:1200px;height:84px;background:var(--purple);color:var(--white);font-size:13px}
.legal-bar .copy{position:absolute;left:178px;top:34px}
.legal-bar .links{position:absolute;right:140px;top:34px}
</style>
</head>
<body>

<header class="site-header">
  <div class="brand"><span class="brand-dot"></span><span class="brand-name">Pippas Party Parlor</span></div>
  <div class="header-phone">CALL: 718-555-0142</div>
  <nav class="main-nav">
    <a href="#">HOME</a><a href="#">ABOUT US</a><a href="#">FUN STUFF</a><a href="#">TESTIMONIALS</a><a href="#">NEWS</a><a href="#">CONTACT US</a>
  </nav>
</header>

<section class="hero">
  <div class="hero-photo" role="img" aria-label="Photo of a clown entertainer in a red hat and striped costume"></div>
  <div class="hero-copy">
    <h1 class="hero-title">AWARD WINNING FAMILY ENTERTAINMENT</h1>
    <p class="hero-quote">"YOUR CHILDREN'S AND FAMILY'S<br>ENTERTAINMENT SPECIALIST"</p>
    <a class="btn">BOOK YOUR PARTY TODAY</a>
  </div>
</section>

<h2 class="services-title">SERVICES</h2>
<div class="services-rule"></div>

<section class="service-grid">
  <div class="service"><div class="service-art" role="img" aria-label="Photo of a child with face paint" style="background:linear-gradient(160deg,#d9c7b8,#8f8f8f)"></div><div class="service-label">FACE PAINTINGS</div></div>
  <div class="service"><div class="service-art" role="img" aria-label="Photo of a magician performing for children" style="background:linear-gradient(160deg,#c9b7a0,#7a6a5e)"></div><div class="service-label">MAGIC SHOWS</div></div>
  <div class="service"><div class="service-art" role="img" aria-label="Photo of a circus clown" style="background:radial-gradient(circle at 50% 35%,#d83a34,#f0e0d0 60%,#2a2a2a)"></div><div class="service-label">CIRCUS CLOWNS</div></div>
  <div class="service"><div class="service-art" role="img" aria-label="Photo of a costumed superhero character" style="background:linear-gradient(180deg,#f2f2f2,#3a3a3a)"></div><div class="service-label">COSTUME CHARACTERS</div></div>
  <div class="service"><div class="service-art" role="img" aria-label="Photo of a smiling party host" style="background:linear-gradient(160deg,#e9b7a0,#b8323a)"></div><div class="service-label">PARTY HOST</div></div>
  <div class="service"><div class="service-art" role="img" aria-label="Photo of carnival party games" style="background:linear-gradient(160deg,#f5e6c0,#c0392b)"></div><div class="service-label">CARNIVAL PARTIES</div></div>
  <div class="service"><div class="service-art" role="img" aria-label="Photo of colourful balloon sculptures" style="background:linear-gradient(160deg,#f3f3f3,#b98fd6 55%,#f3c23a)"></div><div class="service-label">BALLOON SCULPTING</div></div>
  <div class="service"><div class="service-art" role="img" aria-label="Photo of a DJ hosting a party" style="background:linear-gradient(160deg,#1c2340,#4a3a70)"></div><div class="service-label">DJ AND MCS</div></div>
  <div class="service"><div class="service-art" role="img" aria-label="Photo of children in princess dresses" style="background:linear-gradient(160deg,#e9d6c0,#d4a030)"></div><div class="service-label">PRINCESS PARTIES</div></div>
</section>

<section class="welcome">
  <div class="welcome-box">
    <h2 class="welcome-title">WELCOME TO PIPPAS PARTY PARLOR!</h2>
    <p class="welcome-text">Have you ever heard the expression “make your own fun”? Well, when you call Pippas Party Parlor, you don't have to! We bring all the fun you need straight to your door. Clowns, magicians, face painters, balloon artists, jugglers, party princesses, costume characters and much more. Our entertainers create smiles for every age, and we offer a wide range of party services.</p>
    <a class="btn">READ MORE ABOUT US</a>
  </div>
</section>

<section class="contact-strip">
  <div class="contact-item" style="left:260px">
    <svg width="40" height="34" viewBox="0 0 40 34"><path d="M2 16 L38 2 L30 32 L20 22 L14 30 L14 20 Z" fill="var(--purple)"/><path d="M14 20 L38 2" stroke="var(--yellow)" stroke-width="2"/></svg>
    <span>INFO@PIPPASPARTYPARLOR.COM</span>
  </div>
  <div class="contact-item" style="left:792px">
    <svg width="36" height="36" viewBox="0 0 36 36"><path d="M8 2 L14 2 L17 10 L12 14 Q16 22 22 24 L26 19 L34 22 L34 28 Q34 34 28 34 Q4 32 2 8 Q2 2 8 2 Z" fill="var(--purple)"/></svg>
    <span>718-555-0142</span>
  </div>
</section>

<section class="say-hello">
  <h2 class="say-title">Say Hello!</h2>
  <form class="hello-form">
    <div class="field-row"><div class="field">Name</div><div class="field">Email</div></div>
    <div class="field field-area">Message</div>
    <div class="form-submit">SUBMIT</div>
  </form>
</section>

<footer class="site-footer">
  <div class="brand"><span class="brand-dot"></span><span class="brand-name">Pippas Party Parlor</span></div>
  <div class="footer-about">
    <h3 class="footer-heading">ABOUT US</h3>
    <p>Pippa has been performing professionally in the tri-state area since 1996 and has brought her special magic and charm to children's parties ever since, with a show that keeps growing in fun and popularity.</p>
  </div>
  <div class="footer-social">
    <h3 class="footer-heading">SOCIAL</h3>
    <div class="social-row"><span></span><span></span><span></span><span></span><span></span><span></span></div>
  </div>
</footer>

<div class="legal-bar">
  <span class="copy">Pippas Party Parlor Entertainment © 2016. All Rights Reserved.</span>
  <span class="links">Terms of Use | Privacy Policy</span>
</div>

</body>
</html>
```